Stationery Design Project for High End Wealth Management Firm

We need a stationery design for our high-end wealth management firm. Our clientele are affluent and our brand is built around providing investment services with world-class service.

The final concepts should provide a business card, letterhead, and envelope.

We like the idea of having text on the front and back and we MUST have black front and back business cards.
For the business card we have the following that needs to be included:
Company Logo & Tagline
Employee Name
Employee title
Employee Email
Website
2 seperate office cities, addresses, and phone numbers
Financial disclosure (small print)

Having black envelopes would be neat, but black is not a must for the envelopes.
Updates

Project Deadline Extended
Reason: To give the concept one more day of revisions.

Project Deadline Extended
Reason: To allow for more concepts and designs.

Target Market(s)

High Net Worth

Industry/Entity Type

Business

Requirements
Must have
• The following disclosure must be on the back of the card in small print:

Investment Advisory Services offered through Harrowfield Asset Partners LLC, a NFR Registered Investment Advisor. Vantory Wealth Management LLC is not affiliated with Harrowfield Asset Partners LLC.

Black business cards are also a must have.

Please utilize each of the 3 components of our logo in the design.

Please use our white background logo elements when designing our letterhead if you need them.
Nice to have
• Please use our company colors when designing. Utilize a combination of the elements of our logo that we have attached.

We are going to be printing our business cards on letterpress.

```html
<!DOCTYPE html>
<html lang="en">
<head>
<meta charset="utf-8">
<title>Vantory Wealth Management – Stationery</title>
<link href="https://fonts.googleapis.com/css2?family=Cinzel:wght@500&family=Arimo:wght@400&display=swap" rel="stylesheet">
<style>
  :root {
    --ink: #050505;
    --paper: #f7f7f7;
    --gold: #e9bd4e;
    --gold-deep: #c8962e;
    --gold-light: #f6d47a;
    --white: #ffffff;
    --stage: #5a5a5a;
  }
  * { margin: 0; padding: 0; box-sizing: border-box; }
  html, body { width: 1200px; height: 900px; overflow: hidden; }
  body {
    background: var(--stage);
    font-family: "Arimo", Arial, sans-serif;
    position: relative;
  }
  .piece { position: absolute; overflow: hidden; box-shadow: 0 10px 30px rgba(0,0,0,.45); }
  .wave { position: absolute; left: 0; bottom: 0; width: 100%; display: block; z-index: 0; }

  .brand { display: flex; align-items: center; gap: 8px; }
  .brand-dot { width: 22px; height: 22px; border-radius: 50%; background: var(--gold); flex: none; }
  .brand-name {
    font-family: "Cinzel", Georgia, serif; font-weight: 500;
    color: var(--white); letter-spacing: .04em; line-height: 1.05;
  }
  .tagline { color: var(--white); font-size: 10px; letter-spacing: .02em; }
  .contact { color: var(--white); font-size: 10px; line-height: 1.35; }
  .contact .label { color: var(--gold); }
  .site { font-size: 15px; letter-spacing: .14em; z-index: 2; }

  /* Letterhead */
  .letterhead { left: 40px; top: 60px; width: 480px; height: 621px; background: var(--paper); }
  .letterhead-head { position: absolute; left: 0; top: 0; width: 100%; height: 112px; background: var(--ink); }
  .letterhead-head .brand { position: absolute; left: 26px; top: 42px; }
  .letterhead-head .brand-name { font-size: 17px; }
  .letterhead-head .contact { position: absolute; right: 26px; top: 16px; }
  .letterhead-rule {
    position: absolute; left: 0; top: 112px; width: 100%; height: 18px;
    background: linear-gradient(90deg, var(--gold-deep), var(--gold-light), var(--gold));
    font-size: 9px; color: var(--ink); text-align: center; line-height: 18px;
  }
  .letterhead .site { position: absolute; right: 26px; bottom: 36px; color: var(--gold); }

  /* Envelope */
  .envelope { left: 560px; top: 60px; width: 600px; height: 280px; background: var(--ink); }
  .envelope .brand { position: absolute; left: 28px; top: 34px; }
  .envelope .brand-name { font-size: 17px; }
  .envelope .tagline { position: absolute; left: 28px; top: 80px; }
  .envelope .contact { position: absolute; right: 40px; top: 28px; }
  .envelope-window {
    position: absolute; left: 50px; top: 104px; width: 230px; height: 68px;
    background: var(--white); border-radius: 10px; z-index: 1;
  }
  .envelope .site { position: absolute; right: 30px; bottom: 70px; color: var(--ink); }

  /* Business cards */
  .card { top: 380px; width: 290px; height: 166px; background: var(--ink); }
  .card-front { left: 560px; }
  .card-front .brand { position: absolute; left: 26px; top: 50px; }
  .card-front .brand-name { font-size: 17px; }
  .card-front .tagline { position: absolute; left: 26px; top: 98px; font-size: 9px; }
  .card-back { left: 870px; }
  .card-back .brand { position: absolute; left: 16px; top: 30px; gap: 6px; }
  .card-back .brand-dot { width: 16px; height: 16px; }
  .card-back .brand-name { font-size: 12px; }
  .card-holder { position: absolute; right: 16px; top: 30px; text-align: right; }
  .card-holder .name { color: var(--gold); font-size: 10px; letter-spacing: .04em; }
  .card-holder .role { color: var(--white); font-size: 7px; }
  .card-back .contact { position: absolute; left: 16px; top: 84px; font-size: 7.5px; z-index: 2; }
  .card-back .site { position: absolute; right: 14px; bottom: 12px; font-size: 9px; color: var(--ink); }
</style>
</head>
<body>

<section class="piece letterhead" aria-label="Letterhead">
  <header class="letterhead-head">
    <div class="brand"><span class="brand-dot"></span><span class="brand-name">Vantory<br>Wealth Management</span></div>
    <div class="contact">
      <span class="label">Office 1</span> office cities, addresses<br>
      <span class="label">Office 2</span> office cities, addresses<br>
      p : 555 014 2290 | 555 014 2290<br>
      e : danielwhitmore@vantory.com
    </div>
  </header>
  <div class="letterhead-rule">Preferred Wealth Management for Select Individuals</div>
  <svg class="wave" viewBox="0 0 480 200" height="200" preserveAspectRatio="none" aria-hidden="true">
    <path d="M0 130 C120 170 250 40 480 10 L480 200 L0 200 Z" fill="var(--ink)"/>
    <path d="M0 150 C140 190 260 80 400 40 C300 90 170 190 0 175 Z" fill="var(--white)"/>
  </svg>
  <div class="site">www.vantory.com</div>
</section>

<section class="piece envelope" aria-label="Envelope">
  <div class="brand"><span class="brand-dot"></span><span class="brand-name">Vantory<br>Wealth Management</span></div>
  <div class="tagline">Preferred Wealth Management for Select Individuals</div>
  <div class="contact">
    <span class="label">Office 1</span> office cities, addresses<br>
    <span class="label">Office 2</span> office cities, addresses<br>
    p : 555 014 2290 | 555 014 2290<br>
    e : danielwhitmore@vantory.com
  </div>
  <div class="envelope-window"></div>
  <svg class="wave" viewBox="0 0 600 180" height="180" preserveAspectRatio="none" aria-hidden="true">
    <path d="M0 150 C150 150 300 110 420 60 C490 35 550 25 600 25 L600 180 L0 180 Z" fill="var(--gold)"/>
    <path d="M0 130 C180 140 360 60 600 45 L600 65 C380 75 200 165 0 160 Z" fill="var(--ink)"/>
    <path d="M0 118 C200 125 380 30 580 20 C380 45 200 135 0 125 Z" fill="var(--gold-light)"/>
  </svg>
  <div class="site">www.vantory.com</div>
</section>

<section class="piece card card-front" aria-label="Business card front">
  <div class="brand"><span class="brand-dot"></span><span class="brand-name">Vantory<br>Wealth Management</span></div>
  <div class="tagline">Preferred Wealth Management for Select Individuals</div>
</section>

<section class="piece card card-back" aria-label="Business card back">
  <div class="brand"><span class="brand-dot"></span><span class="brand-name">Vantory<br>Wealth Management</span></div>
  <div class="card-holder">
    <div class="name">DANIEL WHITMORE</div>
    <div class="role">Position</div>
  </div>
  <div class="contact">
    <span class="label">Office 1</span> office cities, addresses<br>
    <span class="label">Office 2</span> office cities, addresses<br>
    p : 555 014 2290 | 555 014 2290<br>
    e : danielwhitmore@vantory.com
  </div>
  <svg class="wave" viewBox="0 0 290 90" height="90" preserveAspectRatio="none" aria-hidden="true">
    <path d="M120 60 C180 30 240 15 290 15 L290 90 L40 90 C70 85 95 72 120 60 Z" fill="var(--gold)"/>
    <path d="M0 80 C100 85 180 30 290 35 L290 48 C190 45 110 95 0 90 Z" fill="var(--ink)"/>
    <path d="M0 72 C110 78 190 20 290 22 C190 30 110 90 0 78 Z" fill="var(--gold-light)"/>
  </svg>
  <div class="site">www.vantory.com</div>
</section>

</body>
</html>
```